Accommodation in an Executive Apartment for rent could be a Bed and breakfast,

Currently have a website and like the overall look but it needs revamping and want to add an instant booking button, which I would do later as the unit has a channel manager. Also want to be able to post blogs, etc. Need it to be viewed well on smart phones/tablets. all information related to this unit is on the current site which is www.hollowmerestays.com.au if you would view websites similar to roomvela.com and travonix.com Must be able to be coded in Wordpress

The current design is done in Wordpress so would want this functionality in any new design.

Target Market(s)

Workers at Parliamentary triangle, Canberra. Workers at Marlow centre Deakin, Workers at Westbrook Ellis Hanley Hospital, Workers at Fernvale Hospital, Public Servants Woden, Workers in Deakin ACT

Industry/Entity Type

Accommodation

Number of Pages Required

5+ page

Font styles to use
Sans Serif

Colors
ec1f27

Requirements
Must have
• Must have a classy look about it. Less clicks through the better. Not to wordy. Hard hitting points,
Nice to have
• Would like to retain the same colour theme and look
Should not have
• anything tacky

```html
<!DOCTYPE html>
<html lang="en">
<head>
<meta charset="utf-8">
<title>Hollowmere Stays – Executive Bed &amp; Breakfast</title>
<link rel="stylesheet" href="https://fonts.googleapis.com/css2?family=Roboto:ital,wght@0,300;0,400;0,500;0,700;1,400;1,700&display=swap">
<style>
:root{
  --red:#ec1f27;
  --red-dark:#c8161d;
  --ink:#333333;
  --muted:#777777;
  --line:#dddddd;
  --light:#f1f1f1;
  --panel:#e9e9e9;
  --dark:#2b2b2b;
  --white:#ffffff;
}
*{box-sizing:border-box;margin:0;padding:0}
html,body{width:1200px;height:2436px;overflow:hidden}
body{font-family:"Roboto",Arial,sans-serif;color:var(--ink);background:var(--white);position:relative}
.wrap{width:1000px;margin:0 auto;position:relative}

/* header */
.topbar{height:104px;background:var(--red)}
.topbar .wrap{height:104px;display:flex;align-items:center;justify-content:space-between}
.brand{color:var(--white);font-size:34px;font-weight:400;letter-spacing:.5px}
.call{display:flex;align-items:center;gap:14px;color:var(--white);font-size:17px;font-weight:500;letter-spacing:.5px}
.nav{height:26px;background:var(--white);border-bottom:1px solid var(--line)}
.nav ul{list-style:none;display:flex;justify-content:space-between;height:26px}
.nav li{font-size:11px;font-weight:500;color:#555;line-height:26px;padding:0 26px}
.nav li.active{background:#e4e4e4;color:var(--ink)}

/* hero */
.hero{position:relative;height:470px;background:linear-gradient(180deg,#8fb2c7 0%,#5d8590 30%,#3f6450 52%,#7fa9b9 68%,#5a8396 100%)}
.hero-card{position:absolute;left:100px;top:120px;width:272px;height:176px;background:rgba(255,255,255,.92);padding:20px 18px}
.hero-card h2{color:var(--red);font-style:italic;font-weight:700;font-size:22px}
.hero-card p{font-size:12px;line-height:1.45;color:#444;margin:8px 0 12px}
.btn{display:inline-block;background:var(--red);color:var(--white);font-size:12px;font-weight:500;padding:8px 16px;border-radius:2px}
.btn.dark{background:var(--dark)}
.dots{position:absolute;right:100px;bottom:18px;display:flex;gap:6px}
.dots span{width:9px;height:9px;border-radius:50%;background:rgba(255,255,255,.6)}
.dots span.on{background:var(--white)}

/* availability */
.avail{height:220px;background:var(--panel);padding-top:26px}
.section-title{color:var(--red);font-size:24px;font-weight:500;text-align:center}
.avail-row{display:flex;gap:14px;margin-top:34px;align-items:flex-end}
.field label{display:block;font-size:11px;font-weight:500;color:#555;text-transform:uppercase;margin-bottom:6px}
.field .box{height:30px;background:var(--white);border:1px solid var(--line);font-size:11px;color:#999;padding:8px 10px}
.avail-row .btn{height:30px;padding:8px 20px}

/* rooms */
.rooms{padding-top:40px;height:520px}
.h-left{font-size:28px;font-weight:500;color:var(--ink)}
.lead{font-size:13px;color:var(--muted);line-height:1.5;margin-top:10px;width:700px}
.cards{display:flex;gap:20px;margin-top:30px}
.card{width:235px;border:1px solid var(--line);padding:8px}
.card .photo{height:168px}
.card .row{display:flex;justify-content:space-between;margin-top:12px;font-size:12px;font-weight:500}
.card .price{color:var(--red)}
.stars{color:var(--red);font-size:13px;letter-spacing:2px;margin-top:8px}
.card .btns{display:flex;gap:6px;margin-top:10px}
.card .btns .btn{font-size:10px;padding:6px 12px}

/* blog */
.blog{height:272px;background:linear-gradient(90deg,#1e1e1e,#3a3a3a 60%,#2a2a2a)}
.blog .wrap{display:flex;gap:70px;padding-top:30px}
.badge{width:210px;height:210px;border-radius:50%;background:var(--red);border:6px solid #f26a70;color:var(--white);text-align:center;padding-top:44px;flex:none}
.badge small{font-size:11px;font-weight:700;letter-spacing:1px}
.badge em{display:block;font-size:18px;line-height:1.25;margin:10px 0}
.badge b{font-size:22px}
.post h3{color:var(--white);font-size:26px;font-weight:400}
.post h3 span{font-size:12px;color:#bbb;margin-left:10px}
.post p{color:#bdbdbd;font-size:12px;line-height:1.5;margin-top:10px;width:600px}
.post .btn{margin-top:14px}

/* three columns */
.cols{display:flex;gap:40px;padding-top:36px;height:628px}
.col{width:306px}
.col h4{color:var(--red);font-size:18px;font-weight:500;padding-bottom:10px;border-bottom:2px solid var(--line);margin-bottom:16px}
.event{display:flex;gap:12px;margin-bottom:16px}
.date{width:46px;height:46px;background:var(--red);color:var(--white);text-align:center;font-size:16px;font-weight:700;line-height:1;padding-top:8px;flex:none}
.date small{display:block;font-size:9px;font-weight:400;margin-top:3px}
.event p{font-size:12px;color:var(--muted);line-height:1.45}
.quote{border:1px solid var(--line);padding:14px;font-size:12px;color:var(--muted);line-height:1.5;font-style:italic;position:relative}
.reviewer{display:flex;align-items:center;gap:10px;margin-top:18px;font-size:12px}
.avatar{width:40px;height:40px;border-radius:50%;background:#c9b8a8}
.reviewer b{color:var(--red);font-weight:500}
.gallery{display:grid;grid-template-columns:repeat(3,1fr);gap:6px}
.gallery div{height:64px}

/* footer */
.footer-info{position:absolute;top:2308px;left:0;width:1200px;height:72px;background:var(--panel)}
.footer-info .wrap{display:flex;justify-content:space-between;padding-top:12px;font-size:11px;color:#555}
.footer-info b{display:block;font-size:11px;color:var(--ink);margin-bottom:6px}
.socials{display:flex;gap:5px}
.socials span{width:18px;height:18px;background:#888}
.news{display:flex}
.news .box{width:150px;height:22px;background:var(--white);border:1px solid var(--line)}
.news .btn{font-size:10px;padding:4px 10px}
.footer-bar{position:absolute;top:2380px;left:0;width:1200px;height:56px;background:var(--red);color:var(--white);text-align:center}
.footer-bar ul{list-style:none;display:flex;justify-content:center;gap:36px;font-size:10px;font-weight:500;padding-top:12px}
.footer-bar p{font-size:9px;margin-top:10px;opacity:.9}
</style>
</head>
<body>

<header class="topbar">
  <div class="wrap">
    <div class="brand">Hollowmere Stays</div>
    <div class="call">
      <svg width="18" height="26" viewBox="0 0 18 26"><rect x="1" y="1" width="16" height="24" rx="3" fill="none" stroke="#fff" stroke-width="2"/><circle cx="9" cy="20" r="1.6" fill="#fff"/></svg>
      CALL US TODAY: 02 5550 1847
    </div>
  </div>
</header>
<nav class="nav">
  <ul class="wrap">
    <li class="active">HOME</li><li>B&amp;B ACCOMMODATION</li><li>GALLERY</li><li>WHAT'S NEARBY</li><li>GUEST BOOK</li><li>USEFUL LINKS</li><li>CONTACT US</li>
  </ul>
</nav>

<section class="hero" role="img" aria-label="Poolside patio with a dining table set for breakfast overlooking a lake">
  <div class="hero-card">
    <h2>Brand new Bed &amp; Breakfast</h2>
    <p>Features a separate bedroom and a spacious living area, a well equipped kitchen for self catering and a quiet outdoor terrace.</p>
    <span class="btn">Book Now</span>
  </div>
  <div class="dots"><span class="on"></span><span></span><span></span></div>
</section>

<section class="avail">
  <div class="wrap">
    <h2 class="section-title">Check Availability</h2>
    <div class="avail-row">
      <div class="field" style="width:250px"><label>Your destination</label><div class="box">Enter a destination</div></div>
      <div class="field" style="width:180px"><label>Check in</label><div class="box">dd/mm/yyyy</div></div>
      <div class="field" style="width:180px"><label>Check out</label><div class="box">dd/mm/yyyy</div></div>
      <div class="field" style="width:90px"><label>Rooms</label><div class="box">1</div></div>
      <div class="field" style="width:90px"><label>Adults</label><div class="box">2</div></div>
      <span class="btn">Search Rooms</span>
    </div>
  </div>
</section>

<section class="rooms">
  <div class="wrap">
    <h2 class="h-left">Hotel &amp; Breakfast</h2>
    <p class="lead">A quiet executive base in Deakin, close to the hospitals, the parliamentary triangle and Woden. Modern rooms, fresh breakfasts and secure parking for every guest.</p>
    <div class="cards">
      <div class="card"><div class="photo" role="img" aria-label="Double room with a made bed" style="background:linear-gradient(135deg,#7a2a22,#c9a184)"></div>
        <div class="row"><span>HOTEL DOUBLE ROOM</span><span class="price">$78</span></div><div class="stars">★★★★★</div>
        <div class="btns"><span class="btn">Book</span><span class="btn dark">Details</span></div></div>
      <div class="card"><div class="photo" role="img" aria-label="Family room with two beds" style="background:linear-gradient(135deg,#d8d2c8,#9a8f82)"></div>
        <div class="row"><span>HOTEL FAMILY ROOM</span><span class="price">$78</span></div><div class="stars">★★★★★</div>
        <div class="btns"><span class="btn">Book</span><span class="btn dark">Details</span></div></div>
      <div class="card"><div class="photo" role="img" aria-label="Plated breakfast dishes" style="background:linear-gradient(135deg,#5a2a1a,#b4552e)"></div>
        <div class="row"><span>ROYAL FOODS</span><span class="price">$78</span></div><div class="stars">★★★★★</div>
        <div class="btns"><span class="btn">Book</span><span class="btn dark">Details</span></div></div>
      <div class="card"><div class="photo" role="img" aria-label="Home made food on a white plate" style="background:linear-gradient(135deg,#efe6dc,#c77a4a)"></div>
        <div class="row"><span>HOME MADE FOODS</span><span class="price">$78</span></div><div class="stars">★★★★★</div>
        <div class="btns"><span class="btn">Book</span><span class="btn dark">Details</span></div></div>
    </div>
  </div>
</section>

<section class="blog">
  <div class="wrap">
    <div class="badge"><small>RED HOT SUMMER</small><em>Savings Your Money<br>Every Day Offer!</em><b>Upto 50%</b></div>
    <div class="post">
      <h3>Latest Blog Post <span>22 November 2013</span></h3>
      <p>Our guests often ask where to eat near the hospitals and Woden. This month we round up our favourite cafes, early breakfast spots and quiet dinner places within a short drive.</p>
      <p>We have also added weekly rates for contract workers and public servants staying longer, with flexible check in times and fresh linen twice a week. Ask us about the offer when you book your next stay.</p>
      <span class="btn">Click Here More</span>
    </div>
  </div>
</section>

<section class="wrap cols">
  <div class="col">
    <h4>Upcomming Events</h4>
    <div class="event"><div class="date">12<small>NOV</small></div><p>Spring garden open day at the lakeside park, with music and local food stalls.</p></div>
    <div class="event"><div class="date">18<small>NOV</small></div><p>Night markets in Woden with handmade goods, coffee and street food for all.</p></div>
    <div class="event"><div class="date">24<small>NOV</small></div><p>Twilight concert on the lawns near the parliamentary triangle this weekend.</p></div>
  </div>
  <div class="col">
    <h4>Customer Reviews</h4>
    <div class="quote">"Spotless, quiet and very close to the hospital. The breakfast was generous and the hosts made every late check in easy. I will stay again on my next work trip."</div>
    <div class="reviewer"><div class="avatar" role="img" aria-label="Guest portrait"></div><div><b>Maren Holt</b> ★★★★★</div></div>
  </div>
  <div class="col">
    <h4>Our Gallery</h4>
    <div class="gallery">
      <div role="img" aria-label="Bedroom" style="background:#8a6a55"></div>
      <div role="img" aria-label="Breakfast plate" style="background:#c58a5c"></div>
      <div role="img" aria-label="Dining area" style="background:#6b4a3a"></div>
      <div role="img" aria-label="Pool terrace" style="background:#6f93a3"></div>
      <div role="img" aria-label="Lounge" style="background:#b59b82"></div>
      <div role="img" aria-label="Kitchen" style="background:#d1c3b3"></div>
      <div role="img" aria-label="Garden" style="background:#5f7a4e"></div>
      <div role="img" aria-label="Bathroom" style="background:#c9c3bb"></div>
      <div role="img" aria-label="Entrance" style="background:#7b6658"></div>
    </div>
  </div>
</section>

<footer>
  <div class="footer-info">
    <div class="wrap">
      <div><b>Address</b>14 Ashgrove Lane, Deakin ACT 2600</div>
      <div><b>Phone</b>02 5550 1847<br>stay@hollowmerestays.com.au</div>
      <div><b>Follow us on</b><div class="socials"><span></span><span></span><span></span><span></span><span></span></div></div>
      <div><b>Newsletter Subscribe</b><div class="news"><div class="box"></div><span class="btn">Submit</span></div></div>
    </div>
  </div>
  <div class="footer-bar">
    <ul><li>HOME</li><li>B&amp;B ACCOMMODATION</li><li>GALLERY</li><li>WHAT'S NEARBY</li><li>GUEST BOOK</li><li>USEFUL LINKS</li><li>CONTACT US</li></ul>
    <p>Copyright © 2013 www.hollowmerestays.com.au All rights reserved</p>
  </div>
</footer>

</body>
</html>
```